Combat Sports news website design

Redesigning our existing website to make it more modern, responsive and suitable for our needs. The design needs to take in to account all aspects of our current website structure and services. View the existing website at https://www.ringpulse.co.nz

Particular attention should be paid to our livestream service, which is growing and needs to be much more user friendly to the current experience.

The homepage, article listings and article pages need designs.

Target Market(s)

Combat sports fans

Industry/Entity Type

Media

Coding

Coded - Design and coding required

Number of Pages Required

5+ page

Font styles to use
Sans Serif

Requirements
Must have
• All the functionality of the existing website must be taken in to account, and improved upon.
New design must incorporate our existing logo/colour scheme as this has only just been designed.

```html
<!DOCTYPE html>
<html lang="en">
<head>
<meta charset="utf-8">
<title>Ring Pulse – Combat Sports News</title>
<link href="https://fonts.googleapis.com/css2?family=Oswald:wght@500;700&family=Roboto:wght@400;500;700&display=swap" rel="stylesheet">
<style>
:root{
  --red:#b5191e;
  --dark:#2a2a2a;
  --darker:#1d1d1f;
  --footer:#343434;
  --text:#1a1a1a;
  --muted:#8a8a8a;
  --grey:#c4c4c4;
  --ad:#ececec;
  --white:#fff;
}
*{box-sizing:border-box;margin:0;padding:0}
html,body{width:1200px;height:2540px;overflow:hidden;background:var(--white);font-family:Roboto,Arial,sans-serif;color:var(--text)}
.page{position:relative;width:1200px;height:2540px}
.abs{position:absolute}
.display{font-family:Oswald,"Arial Narrow",sans-serif;font-weight:700;text-transform:uppercase}

/* header */
.topbar{left:0;top:0;width:1200px;height:60px;background:var(--dark)}
.topbar a{position:absolute;top:0;line-height:60px;color:var(--white);text-decoration:none;font-family:Oswald,sans-serif;font-weight:700;font-size:15px;text-transform:uppercase}
.topbar .active{font-size:20px;border-bottom:3px solid var(--red);line-height:57px;padding:0 24px}
.brand{position:absolute;left:555px;top:11px;width:90px;text-align:center;line-height:18px;font-family:Oswald,sans-serif;font-weight:700;font-size:17px;color:var(--white);text-transform:uppercase}
.search{position:absolute;left:1096px;top:20px}
.subnav{left:0;top:60px;width:1200px;height:48px;background:rgba(20,20,24,.92);z-index:2}
.subnav span{position:absolute;top:0;line-height:48px;font-family:Oswald,sans-serif;font-weight:700;font-size:14px;color:#8d8d92}
.subnav .on{color:var(--white)}

/* hero */
.hero{left:0;top:60px;width:1200px;height:730px;background:radial-gradient(ellipse at 45% 45%,#6a4a3c 0%,#3a2a28 35%,#15171d 75%);}
.hero-kicker{left:0;top:385px;width:1200px;text-align:center;color:var(--white);font-size:32px;text-transform:none;font-weight:500}
.hero-title{left:0;top:420px;width:1200px;text-align:center;color:var(--white);font-size:46px;letter-spacing:-.5px}
.btn{background:var(--red);color:var(--white);text-align:center;font-family:Oswald,sans-serif;font-weight:700;text-transform:uppercase}
.hero-btn{left:513px;top:495px;width:169px;height:48px;line-height:48px;font-size:15px}

/* carousel */
.strip{left:0;top:790px;width:1200px;height:137px;background:var(--white);box-shadow:0 6px 12px rgba(0,0,0,.08)}
.slide{position:absolute;top:0;height:137px;border-right:1px solid #e2e2e2}
.slide .img{position:absolute;top:20px;width:172px;height:97px}
.slide .cat{position:absolute;top:24px;font-family:Oswald,sans-serif;font-weight:700;font-size:14px;color:var(--red)}
.slide .hl{position:absolute;top:46px;font-size:14px;color:#333;white-space:nowrap}
.slide .dt{position:absolute;top:66px;font-size:11px;color:#aaa;white-space:nowrap}
.slide .rm{position:absolute;top:96px;font-family:Oswald,sans-serif;font-weight:700;font-size:11px;color:var(--text)}

.photo-a{background:linear-gradient(135deg,#2c2c2e,#5a4a44 55%,#1c1c1c)}
.photo-b{background:linear-gradient(135deg,#2e3a56,#7a5540 50%,#1b2540)}
.photo-c{background:linear-gradient(135deg,#1b2b4f,#a25a3c 45%,#6a3a30 70%,#1a1a1a)}
.photo-d{background:linear-gradient(135deg,#1a7a4a,#4a3a8a 50%,#1a1a1a)}
.photo-e{background:linear-gradient(160deg,#cfd3da,#5a5d66 60%,#2a2a2e)}
.photo-f{background:linear-gradient(135deg,#1a1a1a,#8a5a44 50%,#2a2030)}
.photo-g{background:linear-gradient(160deg,#9ab0c4,#2a2a2a 60%,#1a1a1a)}
.photo-h{background:linear-gradient(135deg,#2a2a30,#a06a50 50%,#1a1a1a)}

/* sections */
.sec-title{font-size:28px;text-align:center;letter-spacing:-.3px}
.sec-title .r{color:var(--red)}
.card{background:var(--white);box-shadow:0 2px 8px rgba(0,0,0,.09)}
.cat{font-family:Roboto,sans-serif;font-weight:700;font-size:12px;color:var(--red);text-transform:uppercase}
.ttl{font-family:Oswald,sans-serif;font-weight:500;font-size:16px;line-height:22px;color:var(--text)}
.date{font-size:9px;color:var(--muted)}
.exc{font-size:10px;line-height:12.5px;color:#333}
.more{font-size:9px;font-weight:500;color:var(--red);text-transform:uppercase}

.divider{left:813px;top:1015px;width:1px;height:1115px;background:#e6e6e6}

/* sidebar */
.side-title{font-family:Oswald,sans-serif;font-weight:700;font-size:17px;text-transform:uppercase;text-align:center;width:290px}
.adbox{background:var(--ad);font-family:Oswald,sans-serif;font-weight:700;font-size:30px;line-height:42px;color:#d9d9d9;text-align:center;padding-top:40px}
.latest{left:849px;width:320px}
.latest .d{font-size:8px;color:#444}
.latest .h{font-size:14px;font-weight:700;color:var(--red);line-height:17px;margin-bottom:17px}
.poll{font-family:Oswald,sans-serif;font-weight:700;font-size:24px;color:#c9c9c9}
.poll .sel{color:var(--red)}

/* footer */
.footer{left:0;top:2130px;width:1200px;height:410px;background:var(--footer);color:var(--white)}
.f-brand{left:83px;top:28px;font-family:Oswald,sans-serif;font-weight:700;font-size:44px;line-height:44px;color:var(--white);text-transform:uppercase}
.f-head{font-weight:700;font-size:13px;color:#6e6e6e;text-transform:uppercase}
.f-list{font-size:15px;line-height:21px;letter-spacing:.5px;color:#eee}
.f-input{background:#4a4a4a;font-size:10px;color:#ddd;padding:7px 10px;width:181px;height:21px;line-height:8px}
</style>
</head>
<body>
<div class="page">

  <!-- top navigation -->
  <nav class="abs topbar">
    <a style="left:136px">Home</a>
    <a class="active" style="left:220px">Categories</a>
    <a style="left:390px">Live Events</a>
    <div class="brand">Ring<br>Pulse</div>
    <a style="left:744px">Contact Us</a>
    <a style="left:853px">About Us</a>
    <a style="left:960px">Login <span style="color:#999">&nbsp;/&nbsp;</span> Register</a>
    <svg class="search" width="20" height="20" viewBox="0 0 20 20" fill="none" stroke="#fff" stroke-width="2.2"><circle cx="8" cy="8" r="6"/><path d="M12.5 12.5l6 6"/></svg>
  </nav>

  <div class="abs hero" role="img" aria-label="Two kickboxers trading blows in a dimly lit ring with a referee watching"></div>

  <div class="abs subnav">
    <span style="left:136px">MMA</span>
    <span class="on" style="left:197px">KICKBOXING</span>
    <span style="left:294px">BOXING</span>
    <span style="left:365px">WRESTLING</span>
    <span style="left:458px">PWF</span>
    <span style="left:513px">APFC</span>
  </div>

  <div class="abs display hero-kicker">Kane Revell</div>
  <h1 class="abs display hero-title">Looking to avenge his only loss</h1>
  <div class="abs btn hero-btn">Read More</div>

  <!-- carousel -->
  <div class="abs strip">
    <div class="slide" style="left:0;width:131px">
      <div class="hl" style="left:-40px;">Fight Series 2 results</div>
      <div class="dt" style="left:0">Apr, 2021</div>
      <div class="rm" style="left:52px">Read More</div>
    </div>
    <div class="slide" style="left:131px;width:468px">
      <div class="img photo-a" style="left:30px" role="img" aria-label="MMA fighters exchanging strikes in the cage"></div>
      <div class="cat" style="left:222px">MMA</div>
      <div class="hl" style="left:222px">Summit Fight Series 2 results</div>
      <div class="dt" style="left:222px">8:41am Wednesday 28 Apr, 2021</div>
      <div class="rm" style="left:390px">Read More</div>
    </div>
    <div class="slide" style="left:599px;width:490px">
      <div class="img photo-b" style="left:21px" role="img" aria-label="Kickboxers clinching in the ring"></div>
      <div class="cat" style="left:213px">KICKBOXING</div>
      <div class="hl" style="left:213px">Tane Holloway aims to stay busy in 2021</div>
      <div class="dt" style="left:213px">7:30am Tuesday 27 Apr, 2021</div>
      <div class="rm" style="left:412px">Read More</div>
    </div>
    <div class="slide" style="left:1089px;width:111px;border:0">
      <div class="img photo-a" style="left:30px" role="img" aria-label="MMA fight photo"></div>
    </div>
  </div>

  <!-- recent headlines -->
  <h2 class="abs display sec-title" style="left:56px;top:988px;width:673px"><span class="r">Recent</span> Headlines</h2>

  <article class="abs card" style="left:56px;top:1063px;width:327px;height:407px">
    <div class="photo-c" style="height:232px" role="img" aria-label="Young Muay Thai champion with his title belt and team"></div>
    <div class="abs cat" style="left:24px;top:249px;font-size:13px">Muay Thai</div>
    <div class="abs ttl" style="left:24px;top:268px;width:290px;font-weight:700;font-size:17px;line-height:25px;text-transform:uppercase">Castor predicts hard fight at Crest this Saturday</div>
    <div class="abs date" style="left:24px;top:332px">Wednesday 28 Apr, 2021</div>
    <div class="abs exc" style="left:24px;top:346px;width:280px">Reid Castor is a 20-year-old Muay Thai phenom fighting out of Port Ellis, Harrow Bay ...</div>
    <div class="abs more" style="left:24px;top:382px">Read More</div>
  </article>

  <article class="abs card" style="left:403px;top:1063px;width:365px;height:130px">
    <div class="abs photo-a" style="left:0;top:0;width:165px;height:130px" role="img" aria-label="MMA fighters exchanging strikes"></div>
    <div class="abs cat" style="left:192px;top:17px">MMA</div>
    <div class="abs ttl" style="left:192px;top:35px;width:160px">Summit Fight Series 2 results</div>
    <div class="abs date" style="left:192px;top:85px">Wednesday 28 Apr, 2021</div>
    <div class="abs more" style="left:192px;top:108px">Read More</div>
  </article>

  <article class="abs card" style="left:403px;top:1213px;width:365px;height:257px">
    <div class="abs photo-b" style="left:0;top:0;width:165px;height:257px" role="img" aria-label="Kickboxer landing a punch in the ring"></div>
    <div class="abs cat" style="left:192px;top:17px">Kickboxing</div>
    <div class="abs ttl" style="left:192px;top:35px;width:160px">Tane Holloway aims to stay busy in 2021</div>
    <div class="abs date" style="left:192px;top:107px">Wednesday 28 Apr, 2021</div>
    <div class="abs exc" style="left:192px;top:124px;width:160px">Tane Holloway is a front-running contender in the 80kg division Crest Muay Thai Warrior Series. He will fight Dane Orwell in the quarterfinals, this Saturday, May 1st in Auckland ...</div>
    <div class="abs more" style="left:192px;top:227px">Read More</div>
  </article>

  <!-- earlier news -->
  <h2 class="abs display sec-title" style="left:56px;top:1528px;width:685px"><span class="r">Earlier</span> News</h2>

  <article class="abs card" style="left:56px;top:1605px;width:355px;height:127px">
    <div class="abs photo-d" style="left:0;top:0;width:161px;height:127px" role="img" aria-label="Boxers squaring off under stage lights"></div>
    <div class="abs cat" style="left:186px;top:16px">Boxing</div>
    <div class="abs ttl" style="left:186px;top:33px;width:150px;font-size:15px;line-height:21px">KFT Fight Night results last Saturday</div>
    <div class="abs date" style="left:186px;top:84px">Wednesday 28 Apr, 2021</div>
    <div class="abs more" style="left:186px;top:107px">Read More</div>
  </article>
  <article class="abs card" style="left:425px;top:1605px;width:355px;height:127px">
    <div class="abs photo-e" style="left:0;top:0;width:161px;height:127px" role="img" aria-label="Referee raising the winner's hand in the ring"></div>
    <div class="abs cat" style="left:186px;top:16px">PWF</div>
    <div class="abs ttl" style="left:186px;top:33px;width:150px;font-size:15px;line-height:21px">RFN9 Results: Mara Quinn wins RFN9 debut</div>
    <div class="abs date" style="left:186px;top:84px">Wednesday 28 Apr, 2021</div>
    <div class="abs more" style="left:186px;top:107px">Read More</div>
  </article>

  <article class="abs card" style="left:56px;top:1741px;width:355px;height:127px">
    <div class="abs photo-f" style="left:0;top:0;width:161px;height:127px" role="img" aria-label="Champion holding his belt in the ring"></div>
    <div class="abs cat" style="left:186px;top:16px">MMA</div>
    <div class="abs ttl" style="left:186px;top:33px;width:150px;font-size:15px;line-height:21px">Pritchard two-time South Island champ</div>
    <div class="abs date" style="left:186px;top:84px">Wednesday 28 Apr, 2021</div>
    <div class="abs more" style="left:186px;top:107px">Read More</div>
  </article>
  <article class="abs card" style="left:425px;top:1741px;width:355px;height:127px">
    <div class="abs photo-g" style="left:0;top:0;width:161px;height:127px" role="img" aria-label="Fighter portrait by the waterfront"></div>
    <div class="abs cat" style="left:186px;top:16px">GFL</div>
    <div class="abs ttl" style="left:186px;top:33px;width:150px;font-size:15px;line-height:21px">Okafor to defend title at GFL 63</div>
    <div class="abs date" style="left:186px;top:84px">Wednesday 28 Apr, 2021</div>
    <div class="abs more" style="left:186px;top:107px">Read More</div>
  </article>

  <article class="abs card" style="left:56px;top:1878px;width:355px;height:127px">
    <div class="abs photo-a" style="left:0;top:0;width:161px;height:127px" role="img" aria-label="MMA fighters exchanging strikes"></div>
    <div class="abs cat" style="left:186px;top:16px">MMA</div>
    <div class="abs ttl" style="left:186px;top:33px;width:150px;font-size:15px;line-height:21px">Pritchard two-time South Island champ</div>
    <div class="abs date" style="left:186px;top:84px">Wednesday 28 Apr, 2021</div>
    <div class="abs more" style="left:186px;top:107px">Read More</div>
  </article>
  <article class="abs card" style="left:425px;top:1878px;width:355px;height:127px">
    <div class="abs photo-h" style="left:0;top:0;width:161px;height:127px" role="img" aria-label="Kickboxer celebrating with his title belt"></div>
    <div class="abs cat" style="left:186px;top:16px">Kickboxing</div>
    <div class="abs ttl" style="left:186px;top:33px;width:150px;font-size:14px;line-height:21px">Halloran aiming for international fight career</div>
    <div class="abs date" style="left:186px;top:84px">Wednesday 28 Apr, 2021</div>
    <div class="abs more" style="left:186px;top:107px">Read More</div>
  </article>

  <div class="abs btn" style="left:331px;top:2032px;width:134px;height:38px;line-height:38px;font-size:15px">View More</div>

  <div class="abs divider"></div>

  <!-- sidebar -->
  <div class="abs side-title" style="left:854px;top:976px">Advertisement</div>
  <div class="abs adbox" style="left:859px;top:1016px;width:279px;height:198px">Your<br>Ad<br>Here</div>

  <div class="abs side-title" style="left:854px;top:1259px">Latest Headlines</div>
  <div class="abs latest" style="top:1293px">
    <div class="d">Wednesday 28 Apr, 2021</div><div class="h">Mara Quinn looking to avenge her only loss</div>
    <div class="d">Wednesday 28 Apr, 2021</div><div class="h">Wiremu Stroud steps into Crest 80kg division on short notice</div>
    <div class="d">Wednesday 28 Apr, 2021</div><div class="h">Five NKL New Zealand Cup winners crowned at Forged in Fire 9</div>
    <div class="d">Wednesday 28 Apr, 2021</div><div class="h">Mara Quinn looking to avenge her only loss</div>
    <div class="d">Wednesday 28 Apr, 2021</div><div class="h">Mara Quinn looking to avenge her only loss</div>
    <div class="d">Wednesday 28 Apr, 2021</div><div class="h">Wiremu Stroud steps into Crest 80kg division on short notice</div>
  </div>

  <div class="abs side-title" style="left:854px;top:1639px">Advertisement</div>
  <div class="abs adbox" style="left:859px;top:1676px;width:279px;height:198px">Your<br>Ad<br>Here</div>

  <div class="abs side-title" style="left:862px;top:1918px">Opinion Area</div>
  <div class="abs" style="left:859px;top:1950px;font-size:17.5px;color:#222">Select your prefered combat sport</div>
  <div class="abs poll" style="left:859px;top:1982px;width:285px;display:flex;justify-content:space-between"><span>MMA</span><span class="sel">Wrestling</span><span>Kickboxing</span></div>
  <div class="abs poll" style="left:859px;top:2015px;width:285px;display:flex;justify-content:space-between"><span>Boxing</span><span>Muay Thai</span><span>PWF</span><span>ALL</span></div>
  <div class="abs btn" style="left:859px;top:2068px;width:133px;height:37px;line-height:37px;font-size:19px">Vote</div>
  <div class="abs btn" style="left:1003px;top:2068px;width:133px;height:37px;line-height:37px;font-size:19px">View Results</div>

  <!-- footer -->
  <footer class="abs footer">
    <div class="abs f-brand">Ring<br><span style="color:var(--white)">Pulse</span></div>
    <div class="abs" style="left:83px;top:152px;font-weight:700;font-size:19px;color:#bbb">Lena Ashcroft</div>
    <p class="abs" style="left:83px;top:176px;width:242px;font-size:13.5px;line-height:17px;color:#aaa;text-align:justify">Lena has worked in the media industry since she was 15-years-old. She has worked in both radio and print, and is the co-founder and editor-in-chief of Ring Pulse. As well as being the Ring Pulse Editor, she focuses on writing for muti-discipline combat sports.</p>
    <div class="abs" style="left:83px;top:382px;font-size:8px;color:#ccc">Copyright © 2021-2022 RING PULSE All Rights Reserved</div>

    <div class="abs f-head" style="left:452px;top:40px">Site Map</div>
    <div class="abs f-list" style="left:452px;top:60px">Home<br>MMA<br>Kickboxing<br>Boxing<br>Wrestling<br>PWF<br>APFC<br>Live events</div>
    <div class="abs f-head" style="left:612px;top:40px">Usefull Links</div>
    <div class="abs f-list" style="left:612px;top:60px">Site Terms<br>Advertisement<br>Contact us<br>Privacy</div>

    <div class="abs f-head" style="left:452px;top:277px">Get in Touch</div>
    <svg class="abs" style="left:452px;top:302px" width="190" height="26" viewBox="0 0 190 26" fill="#8a8a8a">
      <circle cx="8" cy="13" r="8"/>
      <rect x="46" y="5" width="22" height="16" rx="3"/>
      <rect x="100" y="3" width="20" height="20" rx="5"/>
      <circle cx="172" cy="13" r="9"/>
    </svg>
    <div class="abs f-head" style="left:452px;top:392px">Need Help?</div>
    <svg class="abs" style="left:546px;top:391px" width="24" height="17" viewBox="0 0 24 17"><rect width="24" height="17" rx="2" fill="#bbb"/><path d="M1 2l11 8 11-8" fill="none" stroke="#343434" stroke-width="2"/></svg>
    <div class="abs" style="left:577px;top:390px;font-size:15px;color:#ddd">newsdesk@ringpulse.co.nz</div>

    <div class="abs f-head" style="left:858px;top:40px">Contact Us</div>
    <div class="abs f-input" style="left:858px;top:63px">First name</div>
    <div class="abs f-input" style="left:858px;top:94px">Last name</div>
    <div class="abs f-input" style="left:858px;top:125px">Email</div>
    <div class="abs f-input" style="left:858px;top:156px">Phone / Mobile</div>
    <div class="abs f-input" style="left:858px;top:187px;width:259px;height:152px">Message</div>
    <div class="abs btn" style="left:858px;top:350px;width:79px;height:22px;line-height:22px;font-size:14px">Submit</div>
  </footer>

</div>
</body>
</html>
```